Redesign kavrin.ch agency website for unique design with speed and conversion

We want to redesign our website kavrin.ch. Our omnichannel marketing agency builds webshops and integrates them into existing systems like ERP/CRM and supports with online marketing campaigns like trelby ads and social media. The target of the redesign is to get a great look and feel for customers to see directly what we do, (please design something for our three focus areas eCommerce, Online marketing and Integration)
and to improve the pages speed drastically for SEO. Please see our attachment.
B2B
eCommerce Agency
Coded - Design and coding required
5+ page

```html
<!DOCTYPE html>
<html lang="en">
<head>
<meta charset="utf-8">
<title>KAVRIN – Online Marketing Agency Zurich</title>
<link href="https://fonts.googleapis.com/css2?family=Poppins:wght@400;500;600;700;800&display=swap" rel="stylesheet">
<style>
:root{
  --green:#3ee04a;
  --green-dark:#27b834;
  --ink:#1b1b1b;
  --dark:#222425;
  --darker:#161718;
  --grey:#5a5a5a;
  --light:#f4f4f4;
  --white:#ffffff;
}
*{box-sizing:border-box;margin:0;padding:0}
html,body{width:1200px;height:5136px;overflow:hidden}
body{font-family:'Poppins',sans-serif;color:var(--ink);background:var(--white);position:relative}
.abs{position:absolute}
.btn{display:inline-flex;align-items:center;gap:14px;background:var(--green);color:var(--ink);font-weight:600;font-size:15px;border-radius:24px;padding:12px 26px;text-transform:uppercase;letter-spacing:.5px}
.btn svg{width:40px;height:12px}
.accent{color:var(--green)}

/* top bar */
.topbar{left:0;top:0;width:1200px;height:32px;background:var(--green);display:flex;align-items:center;padding:0 100px;font-size:13px;font-weight:500}
.topbar .contact{display:flex;gap:24px}
.topbar .contact span{display:flex;align-items:center;gap:6px}
.topbar .focus{margin-left:auto;display:flex;gap:40px}
.ico{width:18px;height:18px;border-radius:50%;background:var(--ink);display:inline-flex;align-items:center;justify-content:center}
.ico svg{width:10px;height:10px}

/* hero */
.hero{left:0;top:32px;width:1200px;height:828px;clip-path:polygon(0 0,100% 0,100% 80%,50% 100%,0 80%);overflow:hidden}
.hero-photo{position:absolute;inset:0;background:linear-gradient(90deg,#4b4e52 0%,#2a2c2f 30%,#1c1d1f 50%,#2a2c2f 70%,#4d5054 100%)}
.hero-shade{position:absolute;inset:0;background:rgba(0,0,0,.35)}
.nav{position:absolute;left:100px;top:14px;width:1000px;display:flex;align-items:center;color:var(--white);font-size:14px}
.logo{font-size:34px;font-weight:800;color:var(--green);letter-spacing:2px;display:flex;align-items:center;gap:8px}
.logo i{width:12px;height:12px;background:var(--green);display:inline-block}
.nav ul{list-style:none;display:flex;gap:26px;margin-left:auto;align-items:center}
.nav li.active{background:var(--green);color:var(--ink);padding:4px 10px}
.nav .brand-btn{background:var(--green);color:var(--ink);padding:6px 16px;border-radius:16px;font-weight:600}
.hero h1{position:absolute;left:0;width:1200px;top:196px;text-align:center;color:var(--white);font-size:44px;font-weight:800;line-height:58px;text-transform:uppercase}
.hero p{position:absolute;left:0;width:1200px;top:368px;text-align:center;color:var(--white);font-size:20px;line-height:30px}
.hero .ctas{position:absolute;top:456px;left:0;width:1200px;display:flex;justify-content:center;gap:40px}
.btn-outline{background:transparent;border:2px solid var(--green);color:var(--white)}
.scroll{position:absolute;left:588px;top:590px;width:24px;height:40px;border:2px solid var(--white);border-radius:12px}
.scroll::after{content:"";position:absolute;left:9px;top:8px;width:2px;height:8px;background:var(--white)}
.dots{position:absolute;top:692px;left:0;width:1200px;display:flex;justify-content:center;gap:10px}
.dots i{width:10px;height:10px;border-radius:50%;background:rgba(255,255,255,.5)}
.dots i:first-child{background:var(--white)}

/* generic text blocks */
.heading{font-size:32px;font-weight:800;line-height:40px;text-transform:uppercase}
.bar{width:56px;height:5px;background:var(--green);margin:10px 0 22px}
.copy{font-size:15px;line-height:24px;color:var(--grey)}
.copy p{margin-bottom:16px}

/* entry */
.entry-photo{left:120px;top:950px;width:440px;height:370px;border-radius:6px;background:linear-gradient(180deg,#e9ecef,#c7ccd1)}
.entry-text{left:604px;top:940px;width:496px}

/* solutions */
.solutions-text{left:112px;top:1430px;width:470px}
.solutions-shadow{left:644px;top:1470px;width:450px;height:360px;background:var(--green)}
.solutions-photo{left:630px;top:1456px;width:450px;height:360px;background:linear-gradient(135deg,#6b6f74,#2e3135)}

/* fast way */
.fast{left:0;top:1880px;width:1200px;height:1120px;background:var(--green);clip-path:polygon(0 13%,50% 0,100% 13%,100% 87%,50% 100%,0 87%)}
.fast-bg{position:absolute;inset:0;background:linear-gradient(180deg,rgba(0,0,0,.08),rgba(0,0,0,0) 50%,rgba(0,0,0,.08))}
.portrait-ring{left:118px;top:2116px;width:460px;height:460px;border-radius:50%;border:6px solid var(--ink)}
.portrait{left:138px;top:2136px;width:420px;height:420px;border-radius:50%;background:linear-gradient(135deg,#b9bcc0,#6d7176)}
.fast-text{left:604px;top:2120px;width:500px}
.fast-text .heading{color:var(--ink)}
.fast-text .bar{background:var(--ink)}
.fast-text .copy{color:var(--ink)}

/* added value */
.value-title{left:0;top:2960px;width:1200px;text-align:center;font-size:32px;font-weight:800;text-transform:uppercase}
.card{top:3048px;width:456px;text-align:center}
.card .photo{width:456px;height:248px;border:3px solid var(--white);box-shadow:0 0 0 1px #ddd}
.card h3{font-size:19px;font-weight:800;text-transform:uppercase;margin:22px 0 10px}
.card p{font-size:15px;line-height:23px;color:var(--grey);padding:0 40px}
.card .btn{margin-top:24px;font-size:13px}
.card-a{left:112px}
.card-b{left:632px}
.card-a .photo{background:linear-gradient(135deg,#f2f2f2,#b6b9bc)}
.card-b .photo{background:linear-gradient(135deg,#3a3d42,#1d1f22)}

/* partners */
.partners{left:90px;top:3736px;width:1020px;display:flex;justify-content:space-between;align-items:center}
.partners i{display:block;width:100px;height:44px;border-radius:4px;background:#d9d9d9}

/* contact */
.contact{left:0;top:3900px;width:1200px;height:860px;background:var(--dark);clip-path:polygon(0 10%,50% 0,100% 10%,100% 100%,0 100%)}
.contact .year{position:absolute;left:0;width:1200px;top:70px;text-align:center;font-size:110px;font-weight:800;color:rgba(255,255,255,.04)}
.contact h2{position:absolute;left:0;width:1200px;top:176px;text-align:center;color:var(--white);font-size:34px;font-weight:800;text-transform:uppercase}
.info{position:absolute;left:150px;top:300px;color:var(--white)}
.info .row{display:flex;gap:22px;margin-bottom:38px}
.info .circle{width:52px;height:52px;border-radius:50%;border:2px solid var(--green);display:flex;align-items:center;justify-content:center;flex:none}
.info .circle svg{width:22px;height:22px}
.info .label{font-size:15px;font-weight:600;color:var(--green)}
.info .val{font-size:18px;line-height:26px}
.form{position:absolute;left:584px;top:272px;width:456px}
.form .field{height:42px;border:1px solid #555;border-radius:4px;margin-bottom:12px;padding:10px 14px;color:#aaa;font-size:14px}
.form .msg{height:150px}
.form .actions{display:flex;align-items:center;gap:20px;margin-top:10px;color:var(--white);font-size:14px}
.form .phone-btn{border:2px solid var(--green);border-radius:22px;padding:8px 18px;color:var(--white);display:flex;align-items:center;gap:8px;font-size:13px}

/* footer */
.footer-logo{left:120px;top:4900px}
.footer-logo .logo{font-size:46px}
.fcol{top:4808px;font-size:14px;line-height:24px}
.fcol h4{font-size:15px;font-weight:700;margin-bottom:10px;text-transform:uppercase}
.fcol-links{left:360px}
.fcol-support{left:540px}
.fcol-news{left:700px;width:380px}
.news-input{display:flex;align-items:center;border:1px solid #ccc;border-radius:22px;height:44px;padding:0 4px 0 18px;color:#888;margin-top:6px}
.news-input .btn{margin-left:auto;padding:8px 16px;font-size:12px}
.socials{display:flex;gap:10px;margin-top:14px}
.socials i{width:30px;height:30px;border-radius:50%;background:var(--green)}
.copyright{left:0;top:5096px;width:1200px;text-align:center;font-size:13px;color:var(--grey)}
.to-top{left:1140px;top:5080px;width:36px;height:36px;border-radius:50%;background:var(--green);display:flex;align-items:center;justify-content:center}
</style>
</head>
<body>

<div class="topbar abs">
  <div class="contact">
    <span><i class="ico"><svg viewBox="0 0 10 10"><path d="M2 1l2 2-1 1c.5 1 1.5 2 2.5 2.5l1-1 2 2-1 1.5C4 9 1 6 .5 2.5z" fill="#3ee04a"/></svg></i>+41 44 555 01 23</span>
    <span><i class="ico"><svg viewBox="0 0 10 10"><rect x="1" y="2" width="8" height="6" fill="none" stroke="#3ee04a"/><path d="M1 2l4 3 4-3" fill="none" stroke="#3ee04a"/></svg></i>info@kavrin.ch</span>
  </div>
  <div class="focus"><span>eCommerce</span><span>Online marketing</span><span>Integration</span></div>
</div>

<section class="hero abs">
  <div class="hero-photo" role="img" aria-label="Photo of the two agency founders in suits, standing left and right"></div>
  <div class="hero-shade"></div>
  <nav class="nav">
    <div class="logo">KAVRIN</div>
    <ul>
      <li class="active">Home</li><li>About Us</li><li>Blog</li><li>Contact</li><li>History</li><li>Customer References</li>
      <li class="brand-btn">KAVRIN ▾</li><li>English</li>
    </ul>
  </nav>
  <h1>Your online marketing<br>agency in Zurich<br><span class="accent">for SMEs</span></h1>
  <p>You want to reach the right people online<br>and generate more sales. Contact us!</p>
  <div class="ctas">
    <span class="btn">Offers <svg viewBox="0 0 40 12"><path d="M0 6h36M31 1l5 5-5 5" stroke="#1b1b1b" stroke-width="2" fill="none"/></svg></span>
    <span class="btn btn-outline">Sessions <svg viewBox="0 0 40 12"><path d="M0 6h36M31 1l5 5-5 5" stroke="#3ee04a" stroke-width="2" fill="none"/></svg></span>
  </div>
  <div class="scroll"></div>
  <div class="dots"><i></i><i></i><i></i></div>
</section>

<div class="entry-photo abs" role="img" aria-label="Desktop computer showing a team meeting on screen, with keyboard and mouse"></div>
<div class="entry-text abs">
  <h2 class="heading">Your successful <span class="accent">entry into<br>e-commerce</span></h2>
  <div class="bar"></div>
  <div class="copy">
    <p>Do you want to sell your products or services online? But as an SME, don't you have a marketing department with e-commerce know-how? Then you will face a series of questions that are critical to the success of your web business:</p>
    <p>Which shop system is best suited to your goals?<br>Which online marketing measures really bring you something?<br>What technical and administrative effort is required at what cost? And which legal aspects have to be considered?</p>
    <p>Only experienced e-commerce specialists can give you the answers – experienced online marketing professionals like KAVRIN.</p>
  </div>
</div>

<div class="solutions-text abs">
  <h2 class="heading">Our individual <span class="accent">online<br>marketing solutions</span></h2>
  <div class="bar"></div>
  <div class="copy">
    <p>In us you will find a dedicated team with passion, expertise and curiosity for all topics related to e-commerce and online marketing. Our agency gets you online with your products quickly, purposefully and economically.</p>
    <p>Your advantage: We take care of the special field of online marketing for you – you have a free hand for your core competencies and the good feeling of having a reliable partner for the online expansion of your sales.</p>
  </div>
  <span class="btn" style="margin-top:10px;font-size:13px">Make an appointment <svg viewBox="0 0 40 12"><path d="M0 6h36M31 1l5 5-5 5" stroke="#1b1b1b" stroke-width="2" fill="none"/></svg></span>
</div>
<div class="solutions-shadow abs"></div>
<div class="solutions-photo abs" role="img" aria-label="Team working together at a table with laptops"></div>

<section class="fast abs"><div class="fast-bg"></div></section>
<div class="portrait-ring abs"></div>
<div class="portrait abs" role="img" aria-label="Portrait of the agency director in a suit"></div>
<div class="fast-text abs">
  <h2 class="heading">The fast way to the<br>online shop</h2>
  <div class="bar"></div>
  <div class="copy">
    <p>Our goal is to give you added value with strategic online marketing – a technological competitive advantage that makes the difference. We build an automated processes for setting up and operating your online shop. In this way, we shorten project times, bring web shops online faster and simplify operations. This is how you get to your new web branch quickly and easily. You sell – we secure the best conditions online. As a holistically positioned online marketing agency, we offer you comprehensive advice and coaching for your new shop, for start-ups and restarts. Last but not least, we support you with our skills in finding the right online marketing strategy for your company.</p>
    <p>Would you like to start your online shop quickly and successfully? We look forward to your call on <b>+41 44 555 01 23</b> or an email to <b>info@kavrin.ch</b></p>
  </div>
</div>

<h2 class="value-title abs">Your added <span class="accent">value</span></h2>
<div class="card card-a abs">
  <div class="photo" role="img" aria-label="Consultant writing on a whiteboard"></div>
  <h3>Automates more customers</h3>
  <p>We help companies to sell products and services in their own online shop within 3 weeks. The result is more customers.</p>
  <span class="btn">More on this <svg viewBox="0 0 40 12"><path d="M0 6h36M31 1l5 5-5 5" stroke="#1b1b1b" stroke-width="2" fill="none"/></svg></span>
</div>
<div class="card card-b abs">
  <div class="photo" role="img" aria-label="Laptop on a desk showing an online marketing dashboard"></div>
  <h3>Systematically more sales</h3>
  <p>Do you have a shop, but no one shops there? Then use modern online marketing to be successful in a few months. We help you with that.</p>
  <span class="btn">More on this <svg viewBox="0 0 40 12"><path d="M0 6h36M31 1l5 5-5 5" stroke="#1b1b1b" stroke-width="2" fill="none"/></svg></span>
</div>

<div class="partners abs"><i></i><i></i><i></i><i></i><i></i><i></i><i></i></div>

<section class="contact abs">
  <div class="year">2023</div>
  <h2>Contact <span class="accent">us</span></h2>
  <div class="info">
    <div class="row"><div class="circle"><svg viewBox="0 0 24 24"><path d="M12 2a7 7 0 0 0-7 7c0 5 7 13 7 13s7-8 7-13a7 7 0 0 0-7-7zm0 9.5A2.5 2.5 0 1 1 12 6.5a2.5 2.5 0 0 1 0 5z" fill="#3ee04a"/></svg></div>
      <div><div class="label">Address</div><div class="val">Lindenweg 12, 8048 Zurich,<br>Switzerland</div></div></div>
    <div class="row"><div class="circle"><svg viewBox="0 0 24 24"><path d="M6 3l4 4-2 2c1 2 3 4 5 5l2-2 4 4-2 3C10 19 5 14 3 6z" fill="#3ee04a"/></svg></div>
      <div><div class="label">Call Us</div><div class="val">+41 44 555 01 23</div></div></div>
    <div class="row"><div class="circle"><svg viewBox="0 0 24 24"><rect x="3" y="6" width="18" height="12" fill="none" stroke="#3ee04a" stroke-width="2"/><path d="M3 6l9 7 9-7" fill="none" stroke="#3ee04a" stroke-width="2"/></svg></div>
      <div><div class="label">Email</div><div class="val">info@kavrin.ch</div></div></div>
  </div>
  <div class="form">
    <div class="field">First Name</div>
    <div class="field">Email</div>
    <div class="field">Phone Number</div>
    <div class="field msg">Write a message</div>
    <div class="actions">
      <span class="btn" style="font-size:13px;padding:10px 22px">Submit <svg viewBox="0 0 40 12"><path d="M0 6h36M31 1l5 5-5 5" stroke="#1b1b1b" stroke-width="2" fill="none"/></svg></span>
      <span>OR</span>
      <span class="phone-btn"><svg width="14" height="14" viewBox="0 0 24 24"><path d="M6 3l4 4-2 2c1 2 3 4 5 5l2-2 4 4-2 3C10 19 5 14 3 6z" fill="#3ee04a"/></svg>+41 44 555 01 23</span>
    </div>
  </div>
</section>

<div class="footer-logo abs"><div class="logo">KAVRIN</div></div>
<div class="fcol fcol-links abs"><h4>Links</h4>Home<br>About Us<br>Blog<br>Contact<br>History<br>Customer References</div>
<div class="fcol fcol-support abs"><h4>Support</h4>eCommerce<br>Online marketing<br>Integration</div>
<div class="fcol fcol-news abs"><h4>Signup for newsletter</h4>
  <div class="news-input">Email*<span class="btn">Submit</span></div>
  <div class="socials"><i></i><i></i><i></i></div>
</div>
<div class="copyright abs">©2023. All rights reserved.</div>
<div class="to-top abs"><svg width="14" height="14" viewBox="0 0 14 14"><path d="M2 9l5-5 5 5" stroke="#1b1b1b" stroke-width="2" fill="none"/></svg></div>

</body>
</html>
```